Create modern and sleek business card for luxury real estate company

We're a "boutique" real estate office looking for a design that gets across a highly modern luxury brand. Blacks and whites are probably the best colors unless we try a silver foil for the logo. I've attached a version of our current logo here. I'd like to swap out the current font on there with Gotham Light Regular.

I'm looking to have one side of the card have the logo with the space for our agents info on the other side.

Target Market(s)

Young professionals in a "luxury" headspace

Industry/Entity Type

Real estate

Contact Information for Business Card

A place for agent name, cell number, website. The slogan "Simply Rethinking Real Estate".

Font styles to use
Other font styles liked:
• Gotham Regular

Colors

Designer to choose only greyscale colors for use in the design.

Requirements
Must have
• Matte black as the background color. Clean lines and use of contrast. A specific design aspect that will use silver foil.
Nice to have
• Up in the air on integrating a QR code
Should not have
• Any houses or other real estate related design (ex: a clip art house)

```html
<!DOCTYPE html>
<html lang="en">
<head>
<meta charset="utf-8">
<title>Halden Realty – Business Card</title>
<link rel="stylesheet" href="https://fonts.googleapis.com/css2?family=Montserrat:wght@400;500&display=swap">
<style>
  :root {
    --stage: #d9d5d0;
    --card: #ecebe8;
    --ink: #2a2a2a;
    --ink-soft: #4a4a4a;
    --band: #1c1c1c;
  }
  * { margin: 0; padding: 0; box-sizing: border-box; }
  html, body { width: 1200px; height: 887px; overflow: hidden; }
  body { background: var(--stage); font-family: "Montserrat", sans-serif; color: var(--ink); }

  .card {
    position: absolute; left: 100px; top: 171px;
    width: 1000px; height: 544px;
    background: var(--card);
    border-radius: 22px;
    overflow: hidden;
    box-shadow: 0 10px 30px rgba(0,0,0,.12);
  }
  .card-art { position: absolute; inset: 0; }

  .brand {
    position: absolute; left: 66px; top: 62px;
    display: flex; align-items: center; gap: 16px;
  }
  .brand-dot {
    width: 60px; height: 60px; border-radius: 50%;
    border: 2px solid var(--ink);
  }
  .brand-name {
    font-weight: 400; font-size: 30px; line-height: 1.1;
    letter-spacing: 1px; color: var(--ink);
  }

  .agent {
    position: absolute; left: 64px; top: 236px;
  }
  .agent-bar {
    position: absolute; left: 10px; top: 245px;
    width: 6px; height: 55px; background: var(--band);
  }
  .agent-name { font-weight: 500; font-size: 29px; letter-spacing: .5px; }
  .agent-role { font-weight: 400; font-size: 20px; color: var(--ink-soft); margin-top: 4px; letter-spacing: .5px; }

  .contact {
    position: absolute; left: 60px; top: 396px;
    list-style: none;
  }
  .contact li {
    display: flex; align-items: center; gap: 10px;
    font-size: 21px; color: var(--ink-soft); height: 33px; letter-spacing: .3px;
  }
  .contact svg { width: 16px; height: 16px; flex: none; }

  .mark-name {
    position: absolute; left: 516px; top: 247px; width: 400px;
    text-align: center;
    font-weight: 400; font-size: 46px; letter-spacing: 6px; color: var(--ink);
  }
</style>
</head>
<body>
  <div class="card">
    <svg class="card-art" viewBox="0 0 1000 544" width="1000" height="544">
      <rect class="band" x="716" y="0" width="284" height="544" fill="var(--band)"/>
      <circle cx="716" cy="275" r="218" fill="var(--card)" stroke="var(--band)" stroke-width="7"/>
      <circle cx="716" cy="275" r="200" fill="none" stroke="var(--band)" stroke-width="3"/>
    </svg>

    <div class="brand">
      <span class="brand-dot"></span>
      <span class="brand-name">HALDEN<br>REALTY</span>
    </div>

    <span class="agent-bar"></span>
    <div class="agent">
      <p class="agent-name">DANIEL REYES</p>
      <p class="agent-role">Director</p>
    </div>

    <ul class="contact">
      <li>
        <svg viewBox="0 0 16 16"><path d="M4 1.5l2.5 3-1.5 1.5c.8 2 2.5 3.7 4.5 4.5L11 9l3 2.5-1.5 2.5C7 14 2 9 2 3z" fill="none" stroke="currentColor" stroke-width="1.4" stroke-linejoin="round"/></svg>
        360.555.0182
      </li>
      <li>
        <svg viewBox="0 0 16 16"><rect x="1.5" y="3.5" width="13" height="9" rx="1" fill="none" stroke="currentColor" stroke-width="1.4"/><path d="M2 4l6 5 6-5" fill="none" stroke="currentColor" stroke-width="1.4"/></svg>
        hello@haldenhomes.com
      </li>
      <li>
        <svg viewBox="0 0 16 16"><circle cx="8" cy="8" r="6.3" fill="none" stroke="currentColor" stroke-width="1.3"/><ellipse cx="8" cy="8" rx="2.8" ry="6.3" fill="none" stroke="currentColor" stroke-width="1.1"/><path d="M1.7 8h12.6M2.6 5h10.8M2.6 11h10.8" stroke="currentColor" stroke-width="1.1"/></svg>
        www.haldenhomes.com
      </li>
    </ul>

    <p class="mark-name">HALDEN</p>
  </div>
</body>
</html>
```